Coastline Premier Retreats Business Card Design

Design a business card for Coastline Premier Retreats. Look at the website for colors and reference. Card should have logo, name, title, office number, mobile number, email, URL and a tagline like, "Luxury Hotel & Resort Email Marketing" (This might change).

https://www.coastlinepremierretreats.example

The rest I will leave up to your imagination.

Contact Information for Business Card

Logo, name, title, office number, mobile number, email, URL and a tagline like, "Luxury Hotel & Resort Email Marketing" (This might change).

```html
<!DOCTYPE html>
<html lang="en">
<head>
<meta charset="utf-8">
<title>Coastline Premier Retreats – Business Card</title>
<link href="https://fonts.googleapis.com/css2?family=Open+Sans:wght@400;600;700&display=swap" rel="stylesheet">
<style>
  :root {
    --stage: #232323;
    --card: #1f1f22;
    --card-back: #1c1c1e;
    --orange: #f37021;
    --white: #ffffff;
    --emboss: #2b2b2e;
  }
  * { margin: 0; padding: 0; box-sizing: border-box; }
  html, body {
    width: 1200px; height: 780px; overflow: hidden;
    background: var(--stage);
    font-family: "Open Sans", Arial, sans-serif;
  }
  .stage {
    position: relative; width: 1200px; height: 780px;
    display: flex; align-items: center; justify-content: center; gap: 24px;
  }
  .card {
    position: relative; width: 540px; height: 309px;
    background: var(--card); overflow: hidden;
    box-shadow: 0 18px 40px rgba(0,0,0,.45);
  }
  /* front */
  .tagline-band {
    position: absolute; left: 0; top: 0; bottom: 0; width: 66px;
    background: var(--orange);
    display: flex; align-items: center; justify-content: center;
  }
  .tagline {
    transform: rotate(-90deg); white-space: nowrap;
    color: var(--white); font-size: 12.5px; font-weight: 600;
    line-height: 1.25; text-align: center;
  }
  .wordmark {
    position: absolute; right: 36px; top: 34px;
    display: flex; align-items: center; gap: 10px;
    color: var(--white); font-weight: 700; font-size: 19px;
    letter-spacing: .06em; text-transform: uppercase;
  }
  .wordmark .mark-square { width: 14px; height: 14px; background: var(--orange); }
  .person { position: absolute; right: 36px; top: 108px; text-align: right; }
  .person-name { font-size: 27px; font-weight: 700; color: var(--white); line-height: 1.1; }
  .person-name .first { color: var(--orange); }
  .person-title { font-size: 14px; color: var(--white); margin-top: 2px; }
  .edge-tab {
    position: absolute; right: 0; top: 128px; width: 14px; height: 36px;
    background: var(--orange);
  }
  .contacts {
    position: absolute; right: 36px; bottom: 26px;
    list-style: none; text-align: right;
  }
  .contacts li {
    display: flex; justify-content: flex-end; align-items: center; gap: 9px;
    color: var(--white); font-size: 12.5px; line-height: 20px;
  }
  .contacts svg { width: 13px; height: 13px; fill: none; stroke: var(--orange); stroke-width: 2; }
  /* back */
  .card--back { background: var(--card-back); display: flex; align-items: center; justify-content: center; }
  .wordmark--embossed {
    color: var(--emboss); font-weight: 700; font-size: 30px;
    letter-spacing: .06em; text-transform: uppercase; text-align: center; line-height: 1.2;
  }
</style>
</head>
<body>
<main class="stage">
  <section class="card card--front" aria-label="Business card front">
    <div class="tagline-band">
      <p class="tagline">Luxury Hotel &amp;<br>Resort Email Marketing</p>
    </div>
    <div class="wordmark"><span class="mark-square"></span>Coastline Premier Retreats</div>
    <div class="person">
      <p class="person-name"><span class="first">Marisa</span> Kovalen</p>
      <p class="person-title">Co-Founder</p>
    </div>
    <span class="edge-tab"></span>
    <ul class="contacts">
      <li>(555) 214-0386
        <svg viewBox="0 0 24 24"><path d="M5 3h4l2 5-2.5 1.5a11 11 0 0 0 6 6L16 13l5 2v4a2 2 0 0 1-2 2A17 17 0 0 1 3 5a2 2 0 0 1 2-2z"/></svg></li>
      <li>(555) 367-9021
        <svg viewBox="0 0 24 24"><rect x="6" y="2" width="12" height="20" rx="2"/><path d="M11 18h2"/></svg></li>
      <li>www.coastlinepremierretreats.example
        <svg viewBox="0 0 24 24"><circle cx="12" cy="12" r="9"/><path d="M3 12h18M12 3c3 3 3 15 0 18M12 3c-3 3-3 15 0 18"/></svg></li>
      <li>info@coastlinepremierretreats.example
        <svg viewBox="0 0 24 24"><rect x="3" y="5" width="18" height="14" rx="1"/><path d="M3 6l9 7 9-7"/></svg></li>
    </ul>
  </section>

  <section class="card card--back" aria-label="Business card back">
    <p class="wordmark--embossed">Coastline<br>Premier Retreats</p>
  </section>
</main>
</body>
</html>
```